Option Sheet

We need a one page option sheet with a left to right reading of the five options. It should be a one sheet, multiple colors and definitive separations between options This is used in a sales consultation. Backround or colors not in option need to have the follow RGB value (5 red, 20 green, 63 blue)

We added a smaller text file, please change that point

Target Market(s)

Divorce

Industry/Entity Type

Legal

Requirements
Must have
• 1) All five options left to right
• 2)language included in sheet

```html
<!DOCTYPE html>
<html lang="en">
<head>
<meta charset="UTF-8">
<title>Divorce – Five Options</title>
<link href="https://fonts.googleapis.com/css2?family=Montserrat:wght@500;600&family=Source+Sans+3:wght@400;600;700&display=swap" rel="stylesheet">
<style>
  :root {
    --backdrop: #6b6c70;
    --navy: #233e97;
    --navy-line: #1d3488;
    --panel: #b9ced1;
    --card: #ffffff;
    --card-shade: #eef0f2;
    --ink: #2f2f33;
    --red: #e4544f;
    --purple: #6b3f94;
    --orange: #f1953f;
    --green: #2f7a4c;
    --blue: #1d72c2;
    --blue-light: #1ea7e1;
  }
  * { box-sizing: border-box; margin: 0; padding: 0; }
  html, body { width: 1200px; height: 866px; overflow: hidden; }
  body {
    background: var(--backdrop);
    font-family: "Source Sans 3", "Helvetica Neue", Arial, sans-serif;
    color: var(--ink);
    position: relative;
  }
  .sheet {
    position: absolute;
    left: 30px; top: 72px;
    width: 1140px; height: 722px;
    background: var(--panel);
    display: flex;
    flex-direction: column;
  }
  .sheet-header {
    height: 94px;
    background: var(--navy);
    display: flex; align-items: center; justify-content: center;
  }
  .sheet-title {
    font-family: "Montserrat", "Helvetica Neue", Arial, sans-serif;
    font-weight: 500;
    color: #fff;
    font-size: 45px;
    letter-spacing: 0.5px;
  }
  .options {
    flex: 1;
    display: flex;
    gap: 8px;
    padding: 64px 14px 0;
  }
  .option { width: 215px; position: relative; }
  .option-tab {
    position: absolute; left: 20px; right: 20px; top: 0;
    height: 56px;
    border-radius: 16px 16px 0 0;
    color: #fff;
    text-align: center;
    padding-top: 8px;
    line-height: 1.1;
    z-index: 2;
  }
  .option-number { font-weight: 700; font-size: 16px; display: block; }
  .option-name { font-size: 14.5px; display: block; }
  .option-card {
    position: absolute; left: 0; right: 0; top: 22px;
    height: 470px;
    background: linear-gradient(180deg, var(--card-shade) 0%, var(--card) 25%, var(--card) 100%);
    border-radius: 14px;
    overflow: hidden;
    padding: 52px 10px 0;
    box-shadow: 2px 3px 6px rgba(0,0,0,0.15);
  }
  .option-card::after {
    content: ""; position: absolute; left: 0; right: 0; bottom: 0;
    height: 12px; background: var(--accent);
  }
  .group-label {
    text-align: center;
    font-weight: 700;
    font-size: 13.5px;
    color: var(--accent);
    margin-bottom: 4px;
  }
  .point-list { list-style: none; font-size: 12.6px; line-height: 1.15; }
  .point-list li { margin-bottom: 6px; padding-left: 8px; text-indent: -8px; }
  .point-list li::before { content: "• "; }
  .point-list.tight li { margin-bottom: 1px; }
  .divider {
    border: 0; border-top: 1.5px dotted var(--accent);
    margin: 14px 0 12px; opacity: 0.6;
  }
  .option--nothing { --accent: var(--red); }
  .option--counseling { --accent: var(--purple); }
  .option--diy { --accent: var(--orange); }
  .option--limited { --accent: var(--green); }
  .option--hire { --accent: var(--blue); }
  .option--hire .group-label { color: var(--blue-light); }
  .option--hire .point-list li { margin-bottom: 3px; }
  .option-tab { background: var(--accent); }
  .sheet-footer { height: 8px; background: var(--navy-line); }
</style>
</head>
<body>
  <section class="sheet">
    <header class="sheet-header"><h1 class="sheet-title">DIVORCE - FIVE OPTIONS</h1></header>

    <div class="options">
      <article class="option option--nothing">
        <div class="option-tab"><span class="option-number">OPTION #1</span><span class="option-name">Do Nothing</span></div>
        <div class="option-card">
          <h2 class="group-label">ADVANTAGES:</h2>
          <ul class="point-list tight"><li>Stay married</li><li>No life Changes</li></ul>
          <hr class="divider">
          <h2 class="group-label">DISADVANTAGES:</h2>
          <ul class="point-list">
            <li>Remain unhappy, depressed, anxious</li>
            <li>Feel unsafe</li>
            <li>Money and assets may disappear</li>
            <li>Spouse may threaten to leave and/or divorce you</li>
            <li>May cause children to be confused, distressed</li>
            <li>What is going to change?</li>
          </ul>
        </div>
      </article>

      <article class="option option--counseling">
        <div class="option-tab"><span class="option-number">OPTION #2</span><span class="option-name">Go to Counseling</span></div>
        <div class="option-card">
          <h2 class="group-label">ADVANTAGES:</h2>
          <ul class="point-list tight"><li>Reconcile marriage</li><li>Help make a better life</li></ul>
          <hr class="divider">
          <h2 class="group-label">DISADVANTAGES:</h2>
          <ul class="point-list">
            <li>Past issues are highlighted and may drudge up old wounds</li>
            <li>It may just clarify the reasons you need to separate and/or divorce</li>
            <li>There is no quick fix for any situation and BOTH parties must be invested and willing to participate</li>
            <li>Bringing a third party into the marriage may cause more confusion and possible distrust</li>
          </ul>
        </div>
      </article>

      <article class="option option--diy">
        <div class="option-tab"><span class="option-number">OPTION #3</span><span class="option-name">Do it Yourself</span></div>
        <div class="option-card">
          <h2 class="group-label">ADVANTAGES:</h2>
          <ul class="point-list tight"><li>No attorney fees</li><li style="visibility:hidden">&nbsp;</li></ul>
          <hr class="divider">
          <h2 class="group-label">DISADVANTAGES:</h2>
          <ul class="point-list">
            <li>People often find that what is “fair,” may in fact, not be truly fair</li>
            <li>Often times, people do not know the risks</li>
            <li>Complicated legal system</li>
            <li>Unsure how to complete the necessary paperwork and meet the deadlines</li>
            <li>You are too emotional and may be unable to remain clear-headed</li>
            <li>It can be very stressful</li>
          </ul>
        </div>
      </article>

      <article class="option option--limited">
        <div class="option-tab"><span class="option-number">OPTION #4</span><span class="option-name">Limited Representation</span></div>
        <div class="option-card">
          <h2 class="group-label">ADVANTAGES:</h2>
          <ul class="point-list tight"><li>Balance between going alone and our limited involvement in the case</li></ul>
          <hr class="divider" style="margin-top:6px">
          <h2 class="group-label">DISADVANTAGES:</h2>
          <ul class="point-list">
            <li>Our terms may not benefit from our legal knowledge</li>
            <li>The legal consequences of your legal documents will not be explained to you so that you can formulate a plan for handling the rest of your case.</li>
            <li>Your spouse or other parties may cause your legal fees to increase significantly without action on your part</li>
          </ul>
        </div>
      </article>

      <article class="option option--hire">
        <div class="option-tab"><span class="option-number">OPTION #5</span><span class="option-name">Hire Us</span></div>
        <div class="option-card">
          <h2 class="group-label">ADVANTAGES:</h2>
          <ul class="point-list">
            <li>Provide peace of mind</li>
            <li>Often saves you money in the long run</li>
            <li>Can stop problems before they start and advise how actions /events may impact your case</li>
            <li>May be able to come to a settlement agreement sooner</li>
            <li>Lessen the emotional stress of one of the worst things that can happen to a person</li>
            <li>Inform you of your rights and what you are entitled to</li>
            <li>Save you time and energy</li>
            <li>Gain the full benefits of our experience</li>
            <li>Provide a shoulder to lean on and a sounding board</li>
          </ul>
          <hr class="divider" style="margin:8px 0 10px">
          <h2 class="group-label">DISADVANTAGES:</h2>
          <ul class="point-list"><li>Cost</li></ul>
        </div>
      </article>
    </div>

    <div class="sheet-footer"></div>
  </section>
</body>
</html>
```